Design a cool print brochure for an NGO / Give your work a global impact!!

Hi,
I provide a full design brief (below, please scroll) and a mood board (attached) to help you visualize inside my head.. ;-)
I am also available to help and have worked many years in advertising; we will understand each other.
Objective:
To design an A4 folded in two presentation brochure for a non-profit consulting agency called Verdomo.
Verdomo works in sustainability and international development = working with NGO’s, governments and private sector on global issues such as global warming, education for all etc.
Strategy:
This document is a first step in developing a communication strategy. It will be distributed during a major international event called the Brightwater Aid Forum.
Objective:
The double objective of the brochure is:
a) to inform the recipient of what Verdomo is, in the shortest time possible.
b) to showcase relevant projects to demonstrate Verdomo experience and expertise.
Target:
Main target:
Existing Verdomo contacts, such as members of development organizations, NGOs, private sector foundations (CSR), regional networks and other development actors.
NB: the main target already has a certain awareness of Verdomo: we will try to minimize text to maximize visual impact and readability.
Secondary target:
Verdomo will also distribute the brochure to new prospects of interest during the Brightwater Forum.
Timing:
We will need to finalize the design and have the files by June 1st to allow time for print before the event.
Content:
The document should be concise, highly readable (no clutter) and include:
1. text (that we will provide)
and
2. visual elements such as images, shapes and info-graphics (that is you).
NB: Verdomo does not have its own image bank; photos will be provided by you.
Format:
A4 folded in half - 4pp A5 - PORTRAIT FORMAT) with an impactful visual in the front, logo, title and headline (please see examples in the mood board attached).
Design elements:
Verdomo does not have yet a visual identity (please see: http://verdomo.org) so there is room for creativity and no graphic chart to follow.
The sector of consulting in international development is rather conservative but our intention is to be disruptive and create a “Wow” effect. We count on you for that!
Therefore, the design should be “structured”, “organized”, “uncluttered” but also “modern”, “impactful”, “highly visual” (think infographic or mind map to describe our services and projects).
Please, take the time to see the attached presentation: I give you guidelines and examples of what we want and what we like.
We are looking forward to seeing your work and I am available for comments, questions and support.
Thank you.
RK
Target Market(s)
The full brief is in the project description: please, scroll through it.
The target market is : our existing clients base, working in sustainable development (read: NGO and Allied Assembly people)
Industry/Entity Type
Ngo
Font styles to use
Requirements
Must have
- - Design and color elements: please, no black and white. Our company website is in black and white and without graphics; we want the brochure to break away from that and start creating our brand identity; so please, show us colors and desing elements (shapes, backgrounds, etc).
- You have a chance to showcase your talent in terms of visual identity: what lines, forms, layout and colors can you come up with and apply throughout the brochure and serve as the visual identity of Verdomo?
- The structure of the document should be:
- - Front cover: design elements + impacful photo (see mood board example attached) +our logo + this headline: "Collective action for sustainable development and impact"
- - Inside front: a graphic representation of "Our Services": such as core activity in the center circle and satellite circles for the services we offer.
- - Inside back:
- 1. Icons and text boxes for "Our projects"
- 2. A world map of the countries where we have worked. Full list of countries is here:
- http://verdomo.org/experience-1
- - Back cover: our contact + logos of partners.
- Our partners are listed here:
- Please use their original logos (ie, in color).
- The design we will select will serve as a basis for a graphic chart...so more work to come...word to the wise ;)
- Please check out our website verdomo.org to see what we do etc.
Nice to have
- Icons to reflect our services: what icons can you come up with to describe "training services", "building networks" or "program management"?
- I give examples in the mood board.
Should not have
- We are open to creativity and want to generate a "Wow" effect.
- Just note that the sector is rather conservative so flashy colors and cartoon like characters should be avoided. Think "earth, global change, Allied Assembly, climate" without going too green (it's overdone). ;-)
- Make us stand out in the NGO world
- Now you.

```html
<!DOCTYPE html>
<html lang="en">
<head>
<meta charset="utf-8">
<title>Verdomo brochure</title>
<link href="https://fonts.googleapis.com/css2?family=Open+Sans:wght@400;600;700&family=Roboto+Condensed:wght@700&display=swap" rel="stylesheet">
<style>
:root{
  --khaki:#8f8a6f;
  --khaki-dark:#7d785f;
  --map:#a7a18a;
  --green:#6b8e3a;
  --green-light:#a8c08a;
  --brown:#5e5044;
  --slate:#6d7b8a;
  --slate-dark:#3f4f5c;
  --blue-grey:#8e9aa4;
  --ink:#3e3e3e;
  --text:#6a6a6a;
  --paper:#ffffff;
  --backdrop:#e8e8e6;
}
*{margin:0;padding:0;box-sizing:border-box}
html,body{width:878px;height:1200px;overflow:hidden}
body{background:var(--backdrop);font-family:"Open Sans",sans-serif;color:var(--text);position:relative}
.spread{position:absolute;left:39px;width:800px;background:var(--paper);box-shadow:0 2px 8px rgba(0,0,0,.18);overflow:hidden}
.spread--outer{top:18px;height:564px}
.spread--inner{top:618px;height:565px}
.shapes{position:absolute;inset:0;width:800px;height:100%}
.abs{position:absolute}
.brand{font-family:"Open Sans",sans-serif;font-weight:400;font-size:28px;color:#5a5a5a;letter-spacing:.5px;display:flex;align-items:center;gap:8px}
.brand::after{content:"";width:9px;height:9px;background:var(--green)}
.brand--light{color:#fff}
.brand--light::after{background:var(--green-light)}
.intro{left:14px;top:97px;width:335px;font-size:9.6px;line-height:1.35;color:#fff}
.countries{left:14px;top:318px;width:330px;list-style:none;font-size:6.3px;line-height:1.45;color:#fff}
.countries li{position:relative;padding-left:12px;margin-bottom:3px}
.countries li::before{content:"";position:absolute;left:0;top:2px;width:6px;height:6px;background:var(--green)}
.countries b{font-weight:400;color:var(--green-light)}
.contact{left:14px;top:446px;list-style:none;font-size:13.5px;color:#333}
.contact li{display:flex;align-items:center;gap:12px;height:29px}
.contact svg{width:20px;height:20px}
.headline{left:419px;top:428px;font-family:"Roboto Condensed",sans-serif;font-weight:700;font-size:17.5px;line-height:1.22;color:var(--ink);text-transform:uppercase}
.section-title{font-family:"Roboto Condensed",sans-serif;font-weight:700;font-size:17px;color:#fff;top:29px}
.copy{font-size:9.4px;line-height:1.38;color:var(--text)}
.copy p{margin-bottom:9px}
.copy .lead{color:#333;font-weight:600}
.field{left:14px;top:66px;width:370px}
.services-intro{left:411px;top:66px;width:372px;text-align:justify;color:#333;font-weight:600}
.notes{display:flex;gap:16px;font-size:7.6px;line-height:1.4}
.notes p{position:relative;padding-left:16px;flex:1}
.notes p::before{content:"";position:absolute;left:0;top:2px;width:7px;height:7px;background:var(--green)}
.notes--field{left:14px;top:247px;width:370px;color:#333;font-weight:600}
.notes--services{left:418px;top:467px;width:365px;color:#fff}
.notes--services p::before{background:var(--green-light)}
.service{position:absolute;width:88px;height:60px;border-radius:7px;color:#fff;font-size:6.2px;font-weight:600;text-align:center;text-transform:uppercase;line-height:1.3;padding:30px 3px 0;box-shadow:0 2px 3px rgba(0,0,0,.2)}
.service svg{position:absolute;left:34px;top:6px;width:20px;height:20px}
.s1{left:438px;top:150px;background:var(--green-light)}
.s2{left:554px;top:150px;background:var(--blue-grey)}
.s3{left:649px;top:150px;background:var(--green)}
.s4{left:438px;top:363px;background:var(--slate)}
.s5{left:554px;top:363px;background:var(--khaki)}
.s6{left:649px;top:363px;background:var(--slate-dark)}
.hub{left:490px;top:258px;width:193px;height:57px;justify-content:center;font-size:26px}
</style>
</head>
<body>

<section class="spread spread--outer" aria-label="Back and front cover">
  <svg class="shapes" viewBox="0 0 800 564" aria-hidden="true">
    <rect x="0" y="83" width="800" height="332" fill="var(--khaki)"/>
    <line x1="399" y1="0" x2="399" y2="564" stroke="#d8d8d2" stroke-width="1"/>
    <rect x="0" y="537" width="800" height="27" fill="var(--green)"/>
    <line x1="399" y1="537" x2="399" y2="564" stroke="#5f7f33"/>
  </svg>
  <svg class="shapes" viewBox="0 0 800 564" role="img" aria-label="World map showing regions where Verdomo has worked">
    <rect x="16" y="168" width="328" height="124" rx="40" fill="var(--map)"/>
    <g fill="var(--green)">
      <circle cx="73" cy="189" r="5"/><circle cx="180" cy="185" r="5"/><circle cx="255" cy="184" r="5"/><circle cx="187" cy="230" r="5"/>
    </g>
  </svg>
  <svg class="shapes" viewBox="0 0 800 564" role="img" aria-label="Photograph looking up into a glass atrium with a circular structure">
    <defs>
      <linearGradient id="atrium" x1="0" y1="0" x2="1" y2="1">
        <stop offset="0" stop-color="#3e6f95"/><stop offset=".45" stop-color="#a9c6d8"/><stop offset="1" stop-color="#2f4c63"/>
      </linearGradient>
    </defs>
    <polygon points="365,89 800,89 800,410 391,410 348,249" fill="url(#atrium)"/>
  </svg>
  <svg class="shapes" viewBox="0 0 800 564" role="img" aria-label="Photograph of people meeting, tinted green">
    <circle cx="628" cy="401" r="43" fill="var(--green-light)"/>
    <circle cx="729" cy="414" r="80" fill="#fff"/>
    <circle cx="729" cy="414" r="76" fill="#4f7a2c"/>
  </svg>

  <div class="abs brand" style="left:16px;top:22px">Verdomo</div>
  <div class="abs brand" style="left:420px;top:22px">Verdomo</div>

  <p class="abs intro">Verdomo is the result of the collection and examination of all that previous experience. We combine permanently analysis and practice, and incorporate working methods and techniques that encourage active learning and participation.</p>

  <ul class="abs countries">
    <li><b>Europe:</b> EU 28, Norway, Switzerland, Turkey, Montenegro, Ukraine, Serbia, Moldova, Armenia, Georgia and Belarus.</li>
    <li><b>Asia:</b> China, Vietnam, Thailand, Indonesia, Malaysia, Singapore, Bangladesh, Kyrgyzstan, Kazakhstan and Myanmar.</li>
    <li><b>America:</b> US, Canada, Guatemala, El Salvador, Panamá, Costa Rica, Honduras, Colombia, Perú, Bolivia, Brazil, Argentina, Uruguay and Paraguay.</li>
    <li><b>Africa:</b> South Africa, Mozambique, Ethiopia, Kenya, Uganda, Benin, Senegal, Zimbabwe, Ghana, Tunisia, Egypt and Libya.</li>
  </ul>

  <ul class="abs contact">
    <li><svg viewBox="0 0 20 20" aria-hidden="true"><circle cx="10" cy="10" r="9" fill="none" stroke="var(--green)" stroke-width="2"/><path d="M7 6l2 0 1 3-1.5 1a6 6 0 0 0 2.5 2.5L12 11l3 1v2a8 8 0 0 1-8-8z" fill="var(--green)"/></svg>+34 600 410 275</li>
    <li><svg viewBox="0 0 20 20" aria-hidden="true"><circle cx="10" cy="10" r="9" fill="none" stroke="var(--green)" stroke-width="2"/><rect x="5.5" y="7" width="9" height="6.5" fill="var(--green)"/><path d="M5.5 7l4.5 3.5L14.5 7" fill="none" stroke="#fff" stroke-width="1"/></svg>info@verdomo.org</li>
    <li><svg viewBox="0 0 20 20" aria-hidden="true"><circle cx="10" cy="10" r="9" fill="none" stroke="var(--green)" stroke-width="2"/><circle cx="10" cy="10" r="5" fill="none" stroke="var(--green)" stroke-width="1.3"/><path d="M5 10h10M10 5c-2.5 3-2.5 7 0 10M10 5c2.5 3 2.5 7 0 10" fill="none" stroke="var(--green)" stroke-width="1"/></svg>www.verdomo.org</li>
  </ul>

  <h1 class="abs headline">Collective action<br>for sustainable<br>development and<br>impact</h1>
</section>

<section class="spread spread--inner" aria-label="Inside spread">
  <svg class="shapes" viewBox="0 0 800 565" aria-hidden="true">
    <rect x="0" y="14" width="800" height="48" fill="var(--green)"/>
    <rect x="0" y="447" width="800" height="118" fill="var(--khaki)"/>
    <rect x="0" y="447" width="800" height="3" fill="#c9d6b6"/>
    <line x1="399" y1="0" x2="399" y2="565" stroke="#d8d8d2"/>
    <rect x="479" y="246" width="215" height="81" rx="40" fill="#fff" stroke="#cfcfca" stroke-width="1.5"/>
    <rect x="490" y="258" width="193" height="57" rx="28" fill="var(--brown)"/>
    <g fill="none" stroke="#9a9a95" stroke-width="1">
      <path d="M482 211v14h85v22"/><path d="M598 211v36"/><path d="M693 211v14h-80v22"/>
      <path d="M482 363v-18h95v-17"/><path d="M598 363v-32"/><path d="M693 363v-18h-82v-17"/>
    </g>
    <g>
      <circle cx="567" cy="247" r="2.5" fill="#e8915a"/><circle cx="592" cy="247" r="2.5" fill="#e8915a"/><circle cx="613" cy="247" r="2.5" fill="var(--green)"/>
      <circle cx="577" cy="328" r="2.5" fill="var(--slate)"/><circle cx="594" cy="331" r="2.5" fill="#2aa59a"/><circle cx="611" cy="328" r="2.5" fill="#333"/>
    </g>
  </svg>
  <svg class="shapes" viewBox="0 0 800 565" role="img" aria-label="Photograph of a team discussing around a table, tinted green">
    <circle cx="201" cy="422" r="27" fill="var(--green-light)"/>
    <circle cx="106" cy="442" r="94" fill="#fff"/>
    <circle cx="106" cy="442" r="90" fill="#6f8f4c"/>
  </svg>

  <h2 class="abs section-title" style="left:16px">OUR FIELD</h2>
  <h2 class="abs section-title" style="left:412px">VERDOMO SERVICES</h2>

  <div class="abs copy field">
    <p class="lead">Is it possible to deliver effective solutions in the 21st Century without well-managed collaborative action?</p>
    <p>Whether you are a business, a public institution, an NGO or a university; to address global challenges or deliver change at the local level, the capacity to collaborate effectively has become one of the critical elements determining failure from success.</p>
    <p>While that is not new, our own experience shows that more often than not cooperation schemes fail to deliver, precisely because the necessary elements of a collaborative logic are not put in place.</p>
    <p>That is why we decided to create Verdomo: to help our clients integrate the necessary tools, methods and skills to operate effectively in multi-actor complex environments.</p>
  </div>
  <div class="abs notes notes--field">
    <p>In Verdomo we are convinced that the link between research and practice holds an enormous potential for developing solutions to improve our capacity to achieve collective goals.</p>
    <p>In Verdomo we believe that theory cannot be separated from practice. The real background of our work is trying to adapt models to a changing reality.</p>
  </div>

  <p class="abs copy services-intro">Verdomo specializes in the analysis of multi-actor cooperation and the facilitation of processes of change. We believe in the need to improve both the understanding and use of collaborative action. For that, we support value-oriented organisations to integrate a better cooperation logic in their daily practice, whether as part of the internal management process or in the context of their relations with other stakeholders.</p>

  <div class="service s1"><svg viewBox="0 0 20 20" aria-hidden="true"><circle cx="10" cy="10" r="8" fill="none" stroke="#fff" stroke-width="1.6"/><circle cx="10" cy="10" r="4" fill="none" stroke="#fff" stroke-width="1.6"/><circle cx="10" cy="10" r="1.3" fill="#fff"/></svg>Research &amp; analysis of cooperation schemes</div>
  <div class="service s2"><svg viewBox="0 0 20 20" aria-hidden="true"><rect x="4" y="6" width="6" height="12" fill="#fff"/><rect x="11" y="2" width="6" height="16" fill="#fff"/></svg>Facilitation of processes of change</div>
  <div class="service s3"><svg viewBox="0 0 20 20" aria-hidden="true"><circle cx="8" cy="11" r="5" fill="none" stroke="#fff" stroke-width="2.4" stroke-dasharray="2.4 1.6"/><circle cx="15" cy="5" r="3" fill="none" stroke="#fff" stroke-width="1.8"/></svg>Training to improve networked action</div>
  <div class="service s4"><svg viewBox="0 0 20 20" aria-hidden="true"><rect x="7" y="2" width="6" height="5" fill="#fff"/><rect x="2" y="13" width="6" height="5" fill="#fff"/><rect x="12" y="13" width="6" height="5" fill="#fff"/><path d="M10 7v3M5 13v-3h10v3" fill="none" stroke="#fff" stroke-width="1.3"/></svg>Methodologies for organizational change &amp; consensus building</div>
  <div class="service s5"><svg viewBox="0 0 20 20" aria-hidden="true"><rect x="2" y="4" width="14" height="10" fill="none" stroke="#fff" stroke-width="1.6"/><path d="M6 17h6" stroke="#fff" stroke-width="1.6"/><path d="M5 11l3-3 2 2 3-4" fill="none" stroke="#fff" stroke-width="1.3"/></svg>Evaluation of multi-actor projects &amp; programs</div>
  <div class="service s6"><svg viewBox="0 0 20 20" aria-hidden="true"><rect x="3" y="12" width="3" height="6" fill="#fff"/><rect x="8" y="9" width="3" height="9" fill="#fff"/><rect x="13" y="5" width="3" height="13" fill="#fff"/><path d="M3 9l5-4 3 2 6-5" fill="none" stroke="#fff" stroke-width="1.2"/></svg>Coalition building to achieve collective goals</div>

  <div class="abs brand brand--light hub">Verdomo</div>
  <div class="abs brand brand--light" style="left:225px;top:512px">Verdomo</div>

  <div class="abs notes notes--services">
    <p>Our training aims to equip participants with the theoretical and practical tools to approach collaborative schemes in a more effective way. A special focus is placed on comparative analysis, permanent examples and participatory methodologies.</p>
    <p>We are often approached to develop a methodology to support the organization and facilitation of specific meetings or gatherings. Generally, these are meetings where important decisions have to be taken.</p>
  </div>
</section>

</body>
</html>
```